birchwell hollow cattle company website

we would like a home page, an about us page, a page for sires, a page for dams, A sale page where we can list progreny for sale and a contact us. on the about us page we would like there to be a family picture. on the sires page we would like to have a picture of each sire, a description beside them and a link to their online profile at northern hereford registry. on the dam page we would like to have a picture of each dam, aswell as a description beside them aswell as a link to the northern hereford registry site. would like the website to very mobile phone friendly as expecting most traffic to be on phone. we would like the website to look and feel very mich like a farm, rustic, barbed wire and other farm feels. we would also like a frozen genetics pages where we can include pictures and descriptions of the sires and dams aswell as a price for embryos and semen. we need to website to be easy to maintain so we can update pictures and information as it changes, we would like there to be a feature so that people can sign up to be on our mailing list by giving us their mailing addess and email and full name
aswell as an area where they can send us a message to contact us.

leaving for work for 3 weeks in the canadian arctic will have limited ability to use the internet

Target Market(s)

other ranchers, farmers, cattlemen,

Industry/Entity Type

farming, agriculture, cattle

Coding

Coded - Design and coding required

Requirements
Must have
• about page, contact page, sires page, dams page, SALE page.
Nice to have
• country/farm vibe, barbed wire, wood,

```html
<!DOCTYPE html>
<html lang="en">
<head>
<meta charset="utf-8">
<title>Birchwell Hollow Cattle Company</title>
<link href="https://fonts.googleapis.com/css2?family=Bebas+Neue&family=Lato:wght@400;700&display=swap" rel="stylesheet">
<style>
:root{
  --orange:#d7782a;
  --ink:#161616;
  --body:#333;
  --muted:#6b6b6b;
  --beige:#e9dfbf;
  --brown:#4a2816;
  --brown-dark:#3a1f10;
  --grey-bg:#f4f4f4;
  --footer:#3b3b3b;
  --white:#fff;
}
*{box-sizing:border-box;margin:0;padding:0}
html,body{width:1200px;height:3681px;overflow:hidden}
body{position:relative;font-family:'Lato',sans-serif;color:var(--body);background:var(--white)}
.abs{position:absolute}
.display{font-family:'Bebas Neue',sans-serif;color:var(--ink);font-weight:400;letter-spacing:.5px}
.center{left:0;width:1200px;text-align:center}
.divider{position:absolute;height:3px;width:88px;background:var(--beige)}
.btn{position:absolute;display:flex;align-items:center;justify-content:center;background:var(--orange);color:var(--white);font-weight:700;font-size:15px;border-radius:24px;text-decoration:none}
.photo{position:absolute;border-radius:50%}

/* header */
.site-header{position:absolute;left:0;top:0;width:1200px;height:103px;background:var(--white);box-shadow:0 1px 3px rgba(0,0,0,.15);z-index:3}
.brand{position:absolute;left:138px;top:32px;width:150px;text-align:center;font-weight:700;font-size:13px;line-height:18px;color:#2a2a2a;letter-spacing:.5px;white-space:nowrap}
.contact-item{position:absolute;top:14px;display:flex;align-items:center;gap:14px;font-size:14px;color:#333;white-space:nowrap}
.contact-icon{width:38px;height:38px;border-radius:50%;background:var(--brown-dark);display:flex;align-items:center;justify-content:center}
.main-nav{position:absolute;right:143px;top:71px;display:flex;gap:37px;font-size:14px;color:#222;white-space:nowrap}
.main-nav .active{color:var(--orange)}

/* hero */
.hero{position:absolute;left:0;top:103px;width:1200px;height:620px;background:linear-gradient(180deg,#6c7278 0%,#8b8f86 22%,#5b6f45 38%,#7a4a2c 55%,#6a3a22 80%,#4b3322 100%)}
.hero-title{top:162px;font-size:62px;color:var(--white)}
.hero-sub{top:241px;font-size:20px;color:var(--white)}

/* products */
.section-title{font-size:50px}
.intro{top:826px;left:143px;width:914px;text-align:center;font-size:15.5px;line-height:26px;color:#222}
.product-name{position:absolute;width:260px;text-align:center;font-size:18px;color:#222}
.product-desc{position:absolute;width:250px;text-align:center;font-size:13px;line-height:21px;color:var(--muted)}
.arrow{position:absolute;width:24px;height:24px}

/* history */
.history-text{left:667px;top:1722px;width:390px;font-size:14px;line-height:24px;color:var(--muted);text-align:justify}

/* talk */
.talk-text{top:2282px;font-size:18px;line-height:30px;color:var(--white)}

/* program */
.card-name{position:absolute;width:440px;text-align:center;font-size:20px;color:#222}
.card-desc{position:absolute;width:440px;text-align:center;font-size:13.5px;line-height:24px;color:var(--muted)}

/* footer */
.footer-brand{position:absolute;left:128px;top:3452px;width:205px;text-align:center;color:var(--white);font-weight:700;font-size:18px;line-height:26px;letter-spacing:.6px;white-space:nowrap}
.footer-col{position:absolute;top:3343px;color:var(--white)}
.footer-col h3{font-size:16px;font-weight:700;margin-bottom:12px;letter-spacing:.3px}
.footer-col li{list-style:none;font-size:13.5px;line-height:25.7px}
.fc-label{font-size:11px;color:var(--orange);letter-spacing:.3px}
.fc-value{font-size:14px;margin-bottom:13px;white-space:nowrap}
.fc-row{position:relative;padding-left:27px}
.fc-row svg{position:absolute;left:0;top:1px}
.footer-rule{position:absolute;left:143px;top:3569px;width:914px;height:1px;background:#555}
.copyright{top:3580px;font-size:14px;color:var(--white)}
.social{position:absolute;top:3616px;width:34px;height:34px;border-radius:50%;background:var(--white)}
.social.on{background:var(--orange)}
</style>
</head>
<body>

<header class="site-header">
  <div class="brand">BIRCHWELL HOLLOW<br>CATTLE COMPANY</div>
  <div class="contact-item" style="left:613px">
    <span class="contact-icon"><svg width="16" height="12" viewBox="0 0 16 12"><rect x="0" y="0" width="16" height="12" rx="1.5" fill="#fff"/><path d="M1 1.5 L8 7 L15 1.5" stroke="#3a1f10" stroke-width="1.5" fill="none"/></svg></span>
    birchwellhollowcattle@mail.com
  </div>
  <div class="contact-item" style="left:900px">
    <span class="contact-icon"><svg width="16" height="16" viewBox="0 0 24 24"><path fill="#fff" d="M6.6 10.8c1.4 2.8 3.8 5.1 6.6 6.6l2.2-2.2c.3-.3.7-.4 1-.2 1.1.4 2.3.6 3.6.6.6 0 1 .4 1 1V20c0 .6-.4 1-1 1C10.6 21 3 13.4 3 4c0-.6.4-1 1-1h3.5c.6 0 1 .4 1 1 0 1.3.2 2.5.6 3.6.1.3 0 .7-.2 1z"/></svg></span>
    +1 250-555-0147
  </div>
  <nav class="main-nav">
    <span class="active">HOME</span><span>ABOUT US</span><span>SIRES</span><span>DAMS</span><span>FROZEN GENETICS</span><span>SALE</span><span>CONTACT US</span>
  </nav>
</header>

<section class="hero" role="img" aria-label="Red and Hereford cattle at a barbed wire fence in a mountain valley pasture, with a child in front"></section>
<h1 class="abs center display hero-title">BUILT FOR THE PASTURE.PROVEN IN PRODUCTION.</h1>
<p class="abs center hero-sub">Ranch-Ready Angus Bulls &amp; Frozen Genetics Raised Right at Birchwell Hollow.</p>
<a class="btn" style="left:509px;top:297px;width:182px;height:46px;font-size:16px">GET STARTED</a>
<svg class="abs" style="left:0;top:620px" width="1200" height="104" viewBox="0 0 1200 104">
  <path d="M0 80 Q600 -60 1200 80" stroke="#4a2816" stroke-width="6" fill="none"/>
  <path d="M0 104 Q600 -30 1200 104 Z" fill="#fff"/>
</svg>

<h2 class="abs center display section-title" style="top:724px">PRICED TO MOVE, BUILT TO LAST</h2>
<div class="divider" style="left:556px;top:796px"></div>
<p class="abs intro">We are excited so be supplying quality livestock equipment products to interior of BC and surrounding areas. Quality products at competitive prices, we will beat or match products of similar construction. Save yourself the hassle of replacing inferior products that dont last and buy a quality product once. Priced to move, built to last.</p>

<svg class="arrow" style="left:86px;top:1062px" viewBox="0 0 24 24"><path d="M16 3 L7 12 L16 21" stroke="#222" stroke-width="2.5" fill="none"/></svg>
<svg class="arrow" style="left:1090px;top:1062px" viewBox="0 0 24 24"><path d="M8 3 L17 12 L8 21" stroke="#222" stroke-width="2.5" fill="none"/></svg>

<div class="photo" style="left:144px;top:941px;width:266px;height:266px;background:linear-gradient(180deg,#2e6fd0 0%,#6aa4e6 45%,#8a6a45 60%,#b49673 100%)" role="img" aria-label="Deluxe livestock shelter under blue sky"></div>
<div class="photo" style="left:467px;top:941px;width:266px;height:266px;background:linear-gradient(180deg,#9aa0a6 0%,#c9ad7e 40%,#8d7250 75%,#5b5047 100%)" role="img" aria-label="Wooden wind break panel"></div>
<div class="photo" style="left:788px;top:941px;width:266px;height:266px;background:linear-gradient(180deg,#b9bcc0 0%,#a8a39b 45%,#7b6a52 60%,#6b6b6b 100%)" role="img" aria-label="Economy shelter in a muddy yard"></div>

<div class="product-name" style="left:147px;top:1227px">Deluxe Shelters</div>
<div class="product-desc" style="left:152px;top:1258px">These shelters are Grandlanes! 24 feet long 8 feet deep, luxury calf living.</div>
<div class="product-name" style="left:470px;top:1227px">24' Wind Break Panels</div>
<div class="product-desc" style="left:475px;top:1258px">Keep your bovine friends protected from mother natures howling</div>
<div class="product-name" style="left:791px;top:1227px">Economy Shelters</div>
<div class="product-desc" style="left:796px;top:1258px">Clean ergonomic design to keep your calves healthy</div>

<a class="btn" style="left:201px;top:1331px;width:152px;height:42px">LEARN MORE</a>
<a class="btn" style="left:524px;top:1331px;width:152px;height:42px">LEARN MORE</a>
<a class="btn" style="left:845px;top:1331px;width:152px;height:42px">LEARN MORE</a>

<svg class="abs" style="left:0;top:1440px" width="1200" height="1120" viewBox="0 0 1200 1120">
  <defs>
    <linearGradient id="talkBg" x1="0" y1="0" x2="1" y2="1">
      <stop offset="0" stop-color="#4f2b17"/>
      <stop offset=".5" stop-color="#55301b"/>
      <stop offset="1" stop-color="#3f2213"/>
    </linearGradient>
  </defs>
  <rect x="0" y="590" width="1200" height="530" fill="url(#talkBg)" role="img" aria-label="Brown-toned background of cattle in a field"/>
  <path d="M0 117 Q600 -103 1200 117 L1200 607 Q600 755 0 607 Z" fill="#f4f4f4"/>
  <path d="M0 1110 Q600 972 1200 1110 L1200 1120 L0 1120 Z" fill="#fff"/>
</svg>

<div class="photo" style="left:84px;top:1523px;width:526px;height:526px;background:radial-gradient(circle,rgba(0,0,0,0) 60%,#dcdcdc 62%,#e6e6e6 72%,rgba(244,244,244,0) 75%)" role="img" aria-label="Barbed wire wreath ornament"></div>
<div class="photo" style="left:138px;top:1565px;width:442px;height:442px;border:4px solid #4a2816;background:linear-gradient(180deg,#6b4a33 0%,#7d5a3e 35%,#4a3a32 65%,#3c3030 100%)" role="img" aria-label="Family photo in front of a wooden barn door"></div>

<h2 class="abs display section-title" style="left:667px;top:1622px">OUR HISTORY</h2>
<div class="divider" style="left:667px;top:1694px"></div>
<p class="abs history-text">Lorem ipsum dolor sit amet, consectetur adipiscing elit, sed do eiusmod tempor incididunt ut labore et dolore magna aliqua. Ut enim ad minim veniam, quis nostrud exercitation ullamco laboris nisi ut aliquip ex ea commodo consequat. Duis aute irure dolor in reprehenderit in voluptate velit esse cillum dolor</p>
<a class="btn" style="left:667px;top:1874px;width:152px;height:42px">LEARN MORE</a>

<h2 class="abs center display section-title" style="top:2172px;color:#fff">LET’S TALK CATTLE</h2>
<div class="divider" style="left:556px;top:2244px"></div>
<p class="abs center talk-text">Whether you’re looking for herd bulls, females, or frozen genetics, we’re always happy to visit about your<br>program and help you find the right fit.</p>
<a class="btn" style="left:524px;top:2374px;width:152px;height:43px">CONTACT US</a>

<h2 class="abs center display section-title" style="top:2559px">THE CATTLE THAT DRIVE OUR PROGRAM</h2>
<div class="divider" style="left:556px;top:2631px"></div>

<div class="photo" style="left:191px;top:2671px;width:336px;height:336px;background:linear-gradient(180deg,#d9d6d2 0%,#6a3a22 35%,#5c2f1a 70%,#e5e3e0 100%)" role="img" aria-label="Red cow and calf in snow"></div>
<div class="photo" style="left:679px;top:2671px;width:336px;height:336px;background:linear-gradient(180deg,#8fa07a 0%,#5b6a45 30%,#8a4a26 55%,#9a7c4c 100%)" role="img" aria-label="Hereford cows grazing in a pasture"></div>

<div class="card-name" style="left:139px;top:3026px">Herd Sires</div>
<div class="card-desc" style="left:139px;top:3062px">Lorem ipsum dolor sit amet, consectetur adipiscing elit, sed do eiusmod tempor incididunt ut labore et dolore magna aliqua.</div>
<div class="card-name" style="left:627px;top:3026px">Foundation Females</div>
<div class="card-desc" style="left:627px;top:3062px">Lorem ipsum dolor sit amet, consectetur adipiscing elit, sed do eiusmod tempor incididunt ut labore et dolore magna aliqua.</div>
<a class="btn" style="left:284px;top:3136px;width:152px;height:42px">LEARN MORE</a>
<a class="btn" style="left:772px;top:3136px;width:152px;height:42px">LEARN MORE</a>

<footer>
  <div class="abs" style="left:0;top:3195px;width:1200px;height:486px;background:var(--footer)"></div>
  <svg class="abs" style="left:0;top:3190px" width="1200" height="90" viewBox="0 0 1200 90">
    <path d="M0 0 H1200 V5 Q600 145 0 5 Z" fill="#fff"/>
    <path d="M0 14 Q600 152 1200 14" stroke="#4a2816" stroke-width="6" fill="none"/>
  </svg>

  <div class="footer-brand">BIRCHWELL HOLLOW<br>CATTLE COMPANY</div>

  <div class="footer-col" style="left:427px">
    <h3>QUICK LINKS</h3>
    <ul><li>Home</li><li>About Us</li><li>Sires</li><li>Dams</li><li>Frozen Genetics</li><li>Sale</li><li>Contact Us</li></ul>
  </div>
  <div class="footer-col" style="left:636px">
    <h3>LEGAL</h3>
    <ul><li>Site Map</li><li>Privacy Policy</li><li>Terms of Service</li><li>Disclaimer</li></ul>
  </div>
  <div class="footer-col" style="left:844px">
    <h3>CONTACT US</h3>
    <div class="fc-row"><svg width="14" height="14" viewBox="0 0 24 24"><path fill="#d7782a" d="M6.6 10.8c1.4 2.8 3.8 5.1 6.6 6.6l2.2-2.2c.3-.3.7-.4 1-.2 1.1.4 2.3.6 3.6.6.6 0 1 .4 1 1V20c0 .6-.4 1-1 1C10.6 21 3 13.4 3 4c0-.6.4-1 1-1h3.5c.6 0 1 .4 1 1 0 1.3.2 2.5.6 3.6.1.3 0 .7-.2 1z"/></svg><div class="fc-label">PHONE</div><div class="fc-value">+1 250-555-0147</div></div>
    <div class="fc-row"><svg width="15" height="12" viewBox="0 0 16 12"><rect width="16" height="12" rx="1.5" fill="#d7782a"/><path d="M1 1.5 L8 7 L15 1.5" stroke="#3b3b3b" stroke-width="1.4" fill="none"/></svg><div class="fc-label">EMAIL</div><div class="fc-value">birchwellhollowcattle@mail.com</div></div>
    <div class="fc-row"><svg width="12" height="16" viewBox="0 0 12 16"><path fill="#d7782a" d="M6 0C2.7 0 0 2.6 0 5.9 0 10.3 6 16 6 16s6-5.7 6-10.1C12 2.6 9.3 0 6 0zm0 8.2A2.3 2.3 0 1 1 6 3.6a2.3 2.3 0 0 1 0 4.6z"/></svg><div class="fc-label">LOCATION</div><div class="fc-value">Lorem Ipsum dolor 86956</div></div>
  </div>

  <div class="footer-rule"></div>
  <p class="abs center copyright">2026 Copyright - Birchwell Hollow Cattle | All Rights Reserved</p>
  <span class="social" style="left:540px" aria-label="Social link"></span>
  <span class="social on" style="left:582px" aria-label="Social link"></span>
  <span class="social" style="left:623px" aria-label="Social link"></span>
</footer>

</body>
</html>
```